Business Card Design

I need business cards designed for a new company i have started that makes cakes, particularly themed kids cakes with a really modern design and I would like to have my business cards reflect this. I have attached some photos of cakes I have made and would like some to be used.

Industry/Entity Type

Business

Contact Information for Business Card

Business Name: Tarts and Treats by Maren
Mobile: 0492 815 063
email: maren@tartsandtreatsbymaren.example.au
Instagram: instagram.com/tartsandtreatsbymaren/
Facebook: fb.me/tartsandtreatsbymaren

Colors
e667a6
b768aa
3276b5

Requirements
Must have
• Business Name: Tarts and Treats by Maren
• Mobile: 0492 815 063
• email: maren@tartsandtreatsbymaren.example.au
• Instagram: instagram.com/tartsandtreatsbymaren/
• Facebook: fb.me/tartsandtreatsbymaren
Nice to have
• 2 to 3 pictures of my cakes

```html
<!DOCTYPE html>
<html lang="en">
<head>
<meta charset="utf-8">
<title>Tarts and Treats by Maren – Business Card</title>
<link rel="stylesheet" href="https://fonts.googleapis.com/css2?family=Montserrat:wght@400;500;600&display=swap">
<style>
  :root {
    --bg: #ece8ea;
    --plum: #b768aa;
    --plum-deep: #94458f;
    --pink: #e667a6;
    --pink-soft: #f08cbf;
    --white: #ffffff;
    --ink-light: #fbe7f2;
  }
  * { margin: 0; padding: 0; box-sizing: border-box; }
  html, body {
    width: 1200px; height: 843px; overflow: hidden;
    background: var(--bg);
    font-family: "Montserrat", sans-serif;
  }
  .sheet {
    position: relative; width: 1200px; height: 843px;
    display: flex; align-items: center; justify-content: center; gap: 40px;
  }
  .card {
    position: relative; width: 560px; height: 320px;
    border-radius: 4px; overflow: hidden;
    box-shadow: 0 10px 28px rgba(60, 30, 60, 0.22);
  }
  /* Back side */
  .card--back {
    background: linear-gradient(120deg, var(--plum) 0%, #c277b7 45%, var(--plum-deep) 100%);
    display: flex; align-items: center; justify-content: center;
  }
  .brand {
    font-weight: 500; text-align: center; line-height: 1.15;
  }
  .card--back .brand { color: var(--white); font-size: 40px; }
  .brand small { display: block; font-size: 0.5em; letter-spacing: 0.2em; text-transform: uppercase; margin-top: 6px; }
  /* Front side */
  .card--front { background: var(--white); }
  .card--front .brand {
    position: absolute; top: 46px; left: 0; right: 0;
    color: var(--pink); font-size: 32px;
  }
  .wave { position: absolute; inset: 0; width: 100%; height: 100%; }
  .details {
    position: absolute; left: 0; right: 0; top: 206px;
    text-align: center; color: var(--white);
  }
  .details__name { font-size: 17px; font-weight: 600; letter-spacing: 0.04em; }
  .details__role { font-weight: 400; font-size: 15px; letter-spacing: 0; }
  .details__contact { font-size: 12.5px; margin-top: 8px; color: var(--ink-light); }
  .social {
    display: flex; align-items: center; justify-content: center; gap: 8px; margin-top: 12px;
  }
  .social__rule { width: 110px; height: 1px; background: rgba(255,255,255,0.7); }
  .social__dot {
    width: 20px; height: 20px; border-radius: 50%; background: var(--white); opacity: 0.9;
  }
</style>
</head>
<body>
<main class="sheet">
  <section class="card card--back" aria-label="Card back">
    <p class="brand">Tarts and Treats<small>by Maren</small></p>
  </section>

  <section class="card card--front" aria-label="Card front">
    <p class="brand">Tarts and Treats<small>by Maren</small></p>
    <svg class="wave" viewBox="0 0 560 320" preserveAspectRatio="none" aria-hidden="true">
      <defs>
        <linearGradient id="pinkBand" x1="0" y1="0" x2="1" y2="1">
          <stop offset="0" stop-color="#ea75b0"/>
          <stop offset="1" stop-color="#e05f9f"/>
        </linearGradient>
      </defs>
      <path d="M0 170 C 160 160, 380 160, 560 228 L560 236 C 380 172, 160 172, 0 182 Z" fill="var(--plum)"/>
      <path d="M0 188 C 160 178, 380 180, 560 244 L560 320 L0 320 Z" fill="url(#pinkBand)"/>
      <path d="M0 196 C 160 186, 380 190, 560 256" fill="none" stroke="#f6a8cf" stroke-width="1.5"/>
    </svg>
    <div class="details">
      <p class="details__name">LENA HART &nbsp;- <span class="details__role">CEO/Founder</span></p>
      <p class="details__contact">M: 0492 815 063 | E: maren@tartsandtreatsbymaren.example.au</p>
      <div class="social">
        <span class="social__rule"></span>
        <span class="social__dot"></span>
        <span class="social__dot"></span>
        <span class="social__rule"></span>
      </div>
    </div>
  </section>
</main>
</body>
</html>
```